KDWB Business Card

Looking for a business card design to incorporate our branding. We want to only use the colors listing in the Branding Package (attached).
Updates

Target Market(s)

People who need their phone or device fixed.

Industry/Entity Type

Electronics

Contact Information for Business Card

Please use:

Brightwick Gadget Clinic LLC
4810 E Harlow Ridge Rd
Suite 417
San Antonio, TX 78163

Marcus Delgrove, Store Manager

(210) 555-0147

Requirements
Must have
• Must include the colors that are contained within the Branding Package PDF file.

```html
<!DOCTYPE html>
<html lang="en">
<head>
<meta charset="utf-8">
<title>Brightwick Gadget Clinic – Business Card</title>
<link rel="stylesheet" href="https://fonts.googleapis.com/css2?family=Questrial&display=swap">
<style>
  :root {
    --brand-orange: #e8522a;
    --card-white: #ffffff;
    --text-grey: #6b6b6b;
    --text-dark: #3a3a3a;
    --page-bg: #ecebe8;
    --brand-font: "Questrial", "Century Gothic", sans-serif;
  }
  * { box-sizing: border-box; margin: 0; padding: 0; }
  html, body {
    width: 1200px;
    height: 891px;
    overflow: hidden;
    background: var(--page-bg);
    font-family: var(--brand-font);
  }
  .canvas {
    position: relative;
    width: 1200px;
    height: 891px;
  }
  .card {
    position: absolute;
    width: 540px;
    height: 309px;
    border-radius: 6px;
    box-shadow: 0 6px 18px rgba(0,0,0,0.12);
  }
  .card__frame {
    position: absolute;
    inset: 16px;
    border-radius: 22px;
  }
  /* Front */
  .card--front {
    left: 600px;
    top: 130px;
    background: var(--brand-orange);
  }
  .card--front .card__frame { border: 1.5px solid var(--card-white); }
  .brand-mark {
    position: absolute;
    display: flex;
    align-items: center;
    gap: 12px;
  }
  .brand-mark__square {
    width: 30px;
    height: 30px;
    border-radius: 6px;
  }
  .brand-mark__name {
    font-size: 26px;
    letter-spacing: 0.2px;
    white-space: nowrap;
  }
  .card--front .brand-mark {
    left: 50%;
    top: 50%;
    transform: translate(-50%, -50%);
  }
  .card--front .brand-mark__square { background: var(--card-white); }
  .card--front .brand-mark__name { color: var(--card-white); }

  /* Back */
  .card--back {
    left: 60px;
    top: 450px;
    background: var(--card-white);
  }
  .card--back .card__frame { border: 1.5px solid var(--brand-orange); }
  .card--back .brand-mark {
    left: 44px;
    top: 48px;
  }
  .card--back .brand-mark__square { background: var(--brand-orange); width: 26px; height: 26px; }
  .card--back .brand-mark__name { color: var(--brand-orange); font-size: 22px; }

  .contact {
    position: absolute;
    right: 48px;
    bottom: 40px;
    width: 250px;
  }
  .contact__name {
    color: var(--brand-orange);
    font-size: 22px;
    line-height: 1.1;
  }
  .contact__title {
    color: var(--text-grey);
    font-size: 15px;
    margin-bottom: 12px;
  }
  .contact__address {
    font-style: normal;
    color: var(--text-dark);
    font-size: 13px;
    line-height: 1.45;
  }
  .contact__phone {
    color: var(--text-dark);
    font-size: 13px;
    line-height: 1.45;
  }
  .contact__label { color: var(--brand-orange); }
</style>
</head>
<body>
<main class="canvas">
  <section class="card card--front" aria-label="Card front">
    <div class="card__frame"></div>
    <div class="brand-mark">
      <span class="brand-mark__square"></span>
      <span class="brand-mark__name">Brightwick Gadget Clinic</span>
    </div>
  </section>

  <section class="card card--back" aria-label="Card back">
    <div class="card__frame"></div>
    <div class="brand-mark">
      <span class="brand-mark__square"></span>
      <span class="brand-mark__name">Brightwick Gadget Clinic</span>
    </div>
    <div class="contact">
      <p class="contact__name">Marcus Delgrove</p>
      <p class="contact__title">Store Manager</p>
      <address class="contact__address">
        4810 E Harlow Ridge Rd<br>
        Suite 417<br>
        San Antonio, TX 78163
      </address>
      <p class="contact__phone"><span class="contact__label">Phone:</span> (210) 555-0147</p>
    </div>
  </section>
</main>
</body>
</html>
```